Business card design for a dynamic IT consulting company

We need a business card design for a young firm, specialized in the Telecommunications/Consulting industry. The name of the company is Quindor and Partners Business Consulting Ltd. (Short name: Quindor and Partnes)
Quindor = solve read reverse, so we aim to be uncomplicated and solution-oriented. The small pipe in our logo is also related to the word solve. So we need a new business card design, which is simple, eye catching and something non traditional (I would probably prefer a square shaped design rather than a rectangle, but open for suggestions). Attached our logo.

Target Market(s)

Usually our customers are Tier1 Telecoms providers (Q-Netra, Palorix, etc) and their executives.

Industry/Entity Type

Business

Contact Information for Business Card

Name: Bence Tolnavari
Email: b.tolnavari@quindor.hu
Web: www.quindor.hu
Mobile: +36 30 518 2769
Title: Managing Director

Optional:
Company name: Quindor and Partners Ltd.
Address: 1087 Budapest, Tolvenka str. 28/C, Hungary

Font styles to use
Other font styles liked:
• helveticaneue_medium, Prime Regular are used now.

Colors

Designer to choose colors to be used in the design.

Requirements
Must have
• I would like to have a 2 sided design.
Nice to have
• I thought if we make the logo a bit bigger (without the company name), that could go to the back with the company name below. I though, if the pipe in the logo is somehow touchable on the business card, would be nice and unique.

```html
<!DOCTYPE html>
<html lang="en">
<head>
<meta charset="utf-8">
<title>Quindor and Partners – Business Card</title>
<link rel="stylesheet" href="https://fonts.googleapis.com/css2?family=Open+Sans:wght@400;600;700&display=swap">
<style>
  :root {
    --backdrop: #2b2b2b;
    --card: #141414;
    --card-edge: #1c1c1c;
    --ink-white: #f2f2f2;
    --ink-grey: #8a8a8a;
    --accent-blue: #1ba1e2;
    --accent-magenta: #d1339b;
  }
  * { box-sizing: border-box; margin: 0; padding: 0; }
  html, body {
    width: 1200px; height: 900px; overflow: hidden;
    background: var(--backdrop);
    font-family: "Open Sans", Arial, sans-serif;
  }
  .sheet {
    width: 1200px; height: 900px;
    display: flex; align-items: center; justify-content: center; gap: 60px;
  }
  .card {
    width: 500px; height: 290px;
    background: var(--card);
    border: 1px solid var(--card-edge);
    border-radius: 22px;
    display: flex; flex-direction: column; align-items: center; justify-content: center;
    text-align: center;
  }
  .card-front .person-name {
    font-size: 26px; font-weight: 700; color: var(--ink-white); letter-spacing: 0.2px;
  }
  .card-front .person-surname { color: var(--accent-blue); }
  .card-front .person-title {
    font-size: 17px; font-weight: 400; color: var(--ink-white); margin-top: 2px;
  }
  .contact-icons {
    display: flex; gap: 8px; margin: 22px 0 6px;
  }
  .contact-icons svg { width: 13px; height: 13px; fill: var(--accent-blue); }
  .contact-line {
    font-size: 18px; color: var(--ink-white); line-height: 1.35;
  }
  .brand {
    display: flex; align-items: center; gap: 12px;
  }
  .brand-mark {
    width: 18px; height: 18px; background: var(--accent-magenta);
  }
  .brand-name {
    font-size: 36px; font-weight: 400; color: var(--ink-grey); letter-spacing: 0.5px;
  }
</style>
</head>
<body>
<main class="sheet">
  <section class="card card-front">
    <h1 class="person-name">Bence <span class="person-surname">Tolnavari</span></h1>
    <p class="person-title">Managing Director</p>
    <div class="contact-icons">
      <svg viewBox="0 0 16 16" aria-label="phone" role="img"><path d="M3.6 1.2l2.3 2.8-1.3 1.6c.9 2.1 2.6 3.8 4.8 4.8l1.6-1.3 2.8 2.3-1.5 2.6C7 13.8 2.2 9 1 3.1z"/></svg>
      <svg viewBox="0 0 16 16" aria-label="email" role="img"><path d="M1 3h14v10H1z M1.5 3.5L8 9l6.5-5.5" stroke="#141414" stroke-width="1.2"/></svg>
      <svg viewBox="0 0 16 16" aria-label="web" role="img"><circle cx="8" cy="8" r="7"/><path d="M1 8h14M8 1c-3 3.5-3 10.5 0 14M8 1c3 3.5 3 10.5 0 14" stroke="#141414" stroke-width="1" fill="none"/></svg>
    </div>
    <p class="contact-line">+36 30 518 2769</p>
    <p class="contact-line">b.tolnavari@quindor.hu</p>
    <p class="contact-line">www.quindor.hu</p>
  </section>
  <section class="card card-back">
    <div class="brand">
      <span class="brand-mark"></span>
      <span class="brand-name">Quindor &amp; Partners</span>
    </div>
  </section>
</main>
</body>
</html>
```